Stonebrace Business Card Design

The Stonebrace Co is an aggregate (crushing) equipment dealer serving Western Canadian provinces. Stonebrace is a distributor of aggregate equipment for different manufacturers.

We are looking to change and update the existing business card which has been used since the existence of the company. A copy of existing card has been attached for reference. The Stonebrace Co logo we want to remain the same and we want the green color to remain the same.

We are wanting something new with a different look. A refreshing card to show a new modern and updated look. No longer wanting to have the manufacturers on the back of the card but something more like our logo on the back of the card with a statement like "Crushing Solutions"

ideas could be:
- card can be different colors on front and back
- front or reverse of the card could possibly be the green color with the logo in black

Target Market(s)

Owners of Aggregate/Crushing companies

Contact Information for Business Card

see above

Requirements
Must have
• - logo to remain same along with same font within logo
• - green color to remain same
Nice to have
• as noted above under project description
Should not have

```html
<!DOCTYPE html>
<html lang="en">
<head>
<meta charset="utf-8">
<title>Stonebrace Business Card</title>
<link rel="stylesheet" href="https://fonts.googleapis.com/css2?family=Archivo:wght@800&family=Raleway:wght@400;500&family=Open+Sans:wght@400&display=swap">
<style>
  :root {
    --brand-green: #8f8c35;
    --ink: #231f20;
    --paper: #ffffff;
    --backdrop: #dcdcda;
    --cream: #f4f1dc;
  }
  * { margin: 0; padding: 0; box-sizing: border-box; }
  html, body { width: 1200px; height: 1000px; overflow: hidden; }
  body { background: var(--backdrop); position: relative; font-family: "Raleway", sans-serif; }

  .card {
    position: absolute;
    width: 636px;
    height: 363px;
    border-radius: 30px;
    overflow: hidden;
    background: var(--paper);
  }
  .card-front { left: 148px; top: 102px; }
  .card-back { left: 370px; top: 547px; }

  .card-shapes { position: absolute; inset: 0; }

  /* Front */
  .front-brand {
    position: absolute; left: 0; right: 0; top: 108px;
    display: flex; flex-direction: column; align-items: center; gap: 22px;
  }
  .brand-dot {
    width: 86px; height: 86px; border-radius: 50%;
    background: var(--brand-green);
  }
  .front-brand .brand-name {
    font-family: "Archivo", sans-serif; font-weight: 800;
    font-size: 30px; letter-spacing: 0.5px; color: var(--ink);
  }
  .tagline {
    position: absolute; left: 0; right: 0; top: 311px;
    text-align: center; color: var(--paper);
    font-size: 24px; font-weight: 400; letter-spacing: 0.6px;
  }

  /* Back */
  .back-header {
    position: absolute; left: 0; top: 0; width: 100%; height: 131px;
    background: var(--brand-green);
  }
  .holder-name {
    position: absolute; left: 31px; top: 78px;
    color: var(--paper); font-size: 30px; font-weight: 500; letter-spacing: 0.3px;
  }
  .back-brand {
    position: absolute; right: 52px; top: 42px;
    display: flex; flex-direction: column; align-items: center; gap: 10px;
  }
  .back-brand .brand-dot { width: 34px; height: 34px; background: var(--paper); }
  .back-brand .brand-name {
    font-family: "Archivo", sans-serif; font-weight: 800;
    font-size: 15px; color: var(--paper); letter-spacing: 0.2px;
  }

  .contact-list {
    position: absolute; top: 146px;
    list-style: none;
    font-family: "Open Sans", sans-serif; font-size: 23px; color: var(--ink);
  }
  .contact-list li { display: flex; align-items: center; height: 35px; gap: 12px; }
  .contact-list svg { width: 18px; height: 18px; fill: var(--ink); flex: none; }
  .contact-phones { left: 29px; }
  .contact-online { left: 319px; }

  .back-footer {
    position: absolute; left: 0; bottom: 0; width: 100%; height: 98px;
    background: var(--ink);
  }
  .address {
    position: absolute; left: 100px; width: 435px; top: 273px;
    text-align: center; color: var(--cream);
    font-family: "Open Sans", sans-serif; font-size: 14px; letter-spacing: 0.3px;
  }
  .product-lines {
    position: absolute; left: 0; right: 0; top: 312px;
    display: flex; justify-content: center; align-items: center;
    color: var(--paper); font-size: 19px; letter-spacing: 0.4px;
  }
  .product-lines span { padding: 0 12px; }
  .product-lines span + span { border-left: 2px solid var(--paper); }
</style>
</head>
<body>

<section class="card card-front">
  <svg class="card-shapes" viewBox="0 0 636 363" aria-hidden="true">
    <path fill="var(--brand-green)" d="M114 0 L524 0 C508 0 502 44 490 56 Q482 65 468 65 L170 65 Q156 65 148 56 C136 44 130 0 114 0 Z"/>
    <path fill="var(--brand-green)" d="M114 363 L524 363 C508 363 502 318 490 306 Q482 296 468 296 L170 296 Q156 296 148 306 C136 318 130 363 114 363 Z"/>
  </svg>
  <div class="front-brand">
    <div class="brand-dot"></div>
    <div class="brand-name">THE STONEBRACE CO.</div>
  </div>
  <p class="tagline">CRUSHING SOLUTIONS</p>
</section>

<section class="card card-back">
  <div class="back-header"></div>
  <div class="back-footer"></div>
  <svg class="card-shapes" viewBox="0 0 636 363" aria-hidden="true">
    <path fill="var(--brand-green)" d="M98 265 L537 265 C522 265 516 290 500 297 Q494 300 486 300 L150 300 Q142 300 136 297 C120 290 114 265 98 265 Z"/>
  </svg>

  <h1 class="holder-name">DALE MERCER</h1>
  <div class="back-brand">
    <div class="brand-dot"></div>
    <div class="brand-name">THE STONEBRACE CO.</div>
  </div>

  <ul class="contact-list contact-phones">
    <li>
      <svg viewBox="0 0 24 24"><path d="M2 8c0-3 4-5 10-5s10 2 10 5v2h-5V8c-1-1-3-1.5-5-1.5S8 7 7 8v2H2z"/><path d="M6 11h12l3 9H3z"/></svg>
      780 . 555 . 0142
    </li>
    <li>
      <svg viewBox="0 0 24 24"><path d="M6.6 10.8c1.4 2.8 3.8 5.1 6.6 6.6l2.2-2.2c.3-.3.7-.4 1-.2 1.1.4 2.3.6 3.6.6.6 0 1 .4 1 1V20c0 .6-.4 1-1 1C10.6 21 3 13.4 3 4c0-.6.4-1 1-1h3.5c.6 0 1 .4 1 1 0 1.3.2 2.5.6 3.6.1.3 0 .7-.2 1z"/></svg>
      780 . 555 . 0187
    </li>
    <li>
      <svg viewBox="0 0 24 24"><path d="M6 2h12v6H6z"/><path d="M3 9h18v9h-3v-4H6v4H3z"/><path d="M7 15h10v7H7z"/></svg>
      780 . 555 . 0119
    </li>
  </ul>

  <ul class="contact-list contact-online">
    <li>
      <svg viewBox="0 0 24 24"><path d="M2 5h20v2l-10 6L2 7z"/><path d="M2 9l10 6 10-6v10H2z"/></svg>
      dale@stonebr.com
    </li>
    <li>
      <svg viewBox="0 0 24 24"><path fill-rule="evenodd" d="M12 2a10 10 0 1 1 0 20 10 10 0 0 1 0-20zm0 2c-1.2 1.6-2 4-2.2 7h4.4C14 8 13.2 5.6 12 4zm-2.3.4A8 8 0 0 0 4.1 11h3.7c.1-2.5.7-4.8 1.9-6.6zm4.6 0c1.2 1.8 1.8 4.1 1.9 6.6h3.7a8 8 0 0 0-5.6-6.6zM4.1 13a8 8 0 0 0 5.6 6.6c-1.2-1.8-1.8-4.1-1.9-6.6zm5.7 0c.2 3 1 5.4 2.2 7 1.2-1.6 2-4 2.2-7zm6.4 0c-.1 2.5-.7 4.8-1.9 6.6a8 8 0 0 0 5.6-6.6z"/></svg>
      www.stonebrace.ca
    </li>
  </ul>

  <p class="address">2218-48B AVENUE, NISKU, ALBERTA T9E 7R3</p>
  <p class="product-lines"><span>SCREENERS</span><span>CRUSHERS</span><span>STACKERS</span></p>
</section>

</body>
</html>
```